Plakat für Verein
Zielgruppe
Wir möchten eine Veranstaltung für unseren Verein - Hinterbrunnwalder Kameradschaftsbund machen.
Aufgabenstellung
Die Party der Golden 20er
Glanz-Glamour-Lebenslust
Tanzen wie früher - Feiern wie nie
21. März - Uhrzeit: 20.30 im Saal KT
Live mit DJaneWaltraud
Dresscode: Goldene 20er - Fransen, Federn, Hosenträger, Zylinder
Farbe: Gold/Schgwarz

```html
<!DOCTYPE html>
<html lang="de">
<head>
<meta charset="utf-8">
<title>Die Party der Golden 20er – Banner</title>
<link rel="stylesheet" href="https://fonts.googleapis.com/css2?family=Playfair+Display:ital,wght@0,700;0,800;1,700&family=Crimson+Pro:wght@400;600&display=swap">
<style>
  :root {
    --page-bg: #c9c9c9;
    --black: #050505;
    --panel-mid: #3a3b3f;
    --gold-dark: #b9852f;
    --gold: #d7ab4e;
    --gold-light: #f6e2a0;
    --white: #ffffff;
    --badge-ink: #5d8f85;
  }
  * { box-sizing: border-box; margin: 0; padding: 0; }
  html, body { width: 1200px; height: 1117px; overflow: hidden; }
  body {
    background: linear-gradient(180deg, #d4d4d4 0%, #bdbdbd 100%);
    position: relative;
  }
  .banner {
    position: absolute;
    left: 40px;
    top: 333px;
    width: 1724px;
    height: 693px;
    transform: scale(0.65);
    transform-origin: 0 0;
    overflow: hidden;
    background: var(--black);
  }
  .banner__decor {
    position: absolute; inset: 0;
    background:
      radial-gradient(circle at 80% 8%, rgba(255,230,150,0.9) 0, rgba(255,200,80,0.4) 8%, transparent 22%),
      radial-gradient(circle at 95% 60%, rgba(240,170,50,0.7) 0, transparent 25%),
      radial-gradient(circle at 50% 100%, rgba(214,160,70,0.55) 0, transparent 30%),
      radial-gradient(circle at 50% 0%, rgba(214,160,70,0.55) 0, transparent 30%),
      linear-gradient(120deg, #0d0904 0%, #2a1a08 30%, #6b4a1c 50%, #2a1a08 70%, #8a5a18 100%);
  }
  .panel {
    position: absolute;
    left: 72px; top: 63px;
    width: 1580px; height: 567px;
    border: 7px solid var(--gold);
    background: radial-gradient(ellipse 55% 45% at 50% 8%, var(--panel-mid) 0%, #151516 55%, var(--black) 100%);
  }
  .panel__glow {
    position: absolute; inset: 0;
    background:
      radial-gradient(circle at 93% 31%, rgba(255,240,180,0.95) 0, rgba(255,210,110,0.35) 3%, transparent 10%),
      radial-gradient(circle at 87% 95%, rgba(255,240,180,0.9) 0, rgba(255,210,110,0.35) 3%, transparent 11%);
  }
  .title {
    position: absolute; left: 0; right: 0; top: 60px;
    text-align: center;
    font-family: "Playfair Display", serif;
    font-weight: 800;
    font-size: 92px;
    line-height: 1;
    letter-spacing: 1px;
    background: linear-gradient(90deg, var(--gold-dark) 0%, var(--gold) 30%, var(--gold-light) 60%, var(--gold) 80%, var(--gold-dark) 100%);
    -webkit-background-clip: text; background-clip: text;
    color: transparent;
  }
  .tagline {
    position: absolute; left: 0; right: 0; top: 142px;
    text-align: center;
    font-family: "Playfair Display", serif;
    font-style: italic; font-weight: 700;
    font-size: 58px; line-height: 1;
    color: var(--white);
    word-spacing: 6px;
  }
  .tagline .dot { color: var(--gold); font-style: normal; font-size: 40px; vertical-align: 8px; }
  .rule {
    position: absolute; left: 131px; width: 1303px; top: 220px;
    height: 3px; background: var(--gold);
  }
  .condensed {
    display: inline-block;
    transform: scaleX(0.8);
    font-family: "Playfair Display", serif;
    font-weight: 800;
    letter-spacing: -1px;
    white-space: nowrap;
  }
  .motto {
    position: absolute; left: 0; right: 0; top: 240px;
    text-align: center;
    font-size: 60px; line-height: 1;
    color: var(--white);
  }
  .date-ribbon {
    position: absolute; left: 155px; top: 318px;
    width: 1255px; height: 80px;
  }
  .date-ribbon svg { position: absolute; inset: 0; }
  .date-ribbon__text {
    position: absolute; left: 0; right: 0; top: 6px;
    text-align: center;
    font-size: 66px; line-height: 1;
    color: var(--black);
  }
  .live {
    position: absolute; left: 0; right: 0; top: 412px;
    text-align: center;
    font-family: "Crimson Pro", serif;
    font-size: 48px; line-height: 1;
    color: var(--white);
  }
  .live__dj { color: var(--gold); font-weight: 600; }
  .dresscode {
    position: absolute; left: 0; right: 0; top: 485px;
    text-align: center;
    font-family: "Crimson Pro", serif;
    font-weight: 600;
    font-size: 29px; line-height: 1;
    color: var(--white);
    letter-spacing: -0.3px;
  }
  .dresscode__label { color: var(--gold); }
  .dresscode__sep { margin: 0 14px; font-weight: 400; }
  .club-badge {
    position: absolute; left: 39px; top: 467px;
    width: 196px; height: 196px; border-radius: 50%;
    background: var(--white);
    display: flex; align-items: center; justify-content: center;
    text-align: center;
    padding: 24px;
    font-family: "Crimson Pro", serif;
    font-weight: 600;
    font-size: 22px; line-height: 1.15;
    color: var(--badge-ink);
  }
</style>
</head>
<body>
  <section class="banner" aria-label="Banner: Die Party der Golden 20er">
    <div class="banner__decor" role="img" aria-label="Goldene Art-déco-Streifen mit Lichtfunken auf schwarzem Grund"></div>
    <div class="panel">
      <div class="panel__glow" role="img" aria-label="Goldene Lichtfunken"></div>
      <h1 class="title">DIE PARTY DER GOLDEN 20ER</h1>
      <p class="tagline">Glanz <span class="dot">•</span> Glamour <span class="dot">•</span> Lebenslust</p>
      <div class="rule"></div>
      <p class="motto"><span class="condensed">TANZEN WIE FRÜHER - FEIERN WIE NIE</span></p>
      <div class="date-ribbon">
        <svg width="1255" height="80" viewBox="0 0 1255 80" aria-hidden="true">
          <defs>
            <linearGradient id="ribbonGold" x1="0" x2="1" y1="0" y2="0">
              <stop offset="0" stop-color="#b47f2c"/>
              <stop offset="0.35" stop-color="#d9b05a"/>
              <stop offset="0.7" stop-color="#f7e4a3"/>
              <stop offset="1" stop-color="#c9953c"/>
            </linearGradient>
          </defs>
          <polygon points="0,80 38,40 0,0 1255,0 1217,40 1255,80" fill="url(#ribbonGold)"/>
        </svg>
        <p class="date-ribbon__text"><span class="condensed">21. MÄRZ - UHRZEIT: 20.30 IM SAAL KT</span></p>
      </div>
      <p class="live">Live mit <span class="live__dj">DJaneWaltraud</span></p>
      <p class="dresscode"><span class="dresscode__label">Dresscode:</span> Goldene 20er - Fransen, Federn, Hosenträger, Zylinder<span class="dresscode__sep">|</span>Farbe: Gold/Schgwarz</p>
    </div>
    <div class="club-badge">Hinterbrunnwalder Kameradschaftsbund</div>
  </section>
</body>
</html>
```